TalkHarbor - Language Coaching Services

Sleek, innovative, trendy design for Language Coaching business.

TalkHarbor is a new UK based company that provides Language Coaching services. We offer highly personalized on-line and face to face language courses. We also impart learning techniques workshops based on the latest neuroscience research for second-language acquisition.

Target Market(s)

See attached info

Industry/Entity Type

Consulting

Contact Information for Business Card

TalkHarbor
DaniaKV@talkharbor.co.uk
TalkHarbor.co.uk
London, UK

Font styles to use
Sans Serif

```html
<!DOCTYPE html>
<html lang="en">
<head>
<meta charset="utf-8">
<title>TalkHarbor Business Card</title>
<link rel="stylesheet" href="https://fonts.googleapis.com/css2?family=Roboto:wght@300;400;500;700&family=Roboto+Condensed:wght@400;700&display=swap">
<style>
  :root {
    --bg: #3a3d42;
    --card-white: #f4f5f6;
    --navy: #0b5e8e;
    --deep: #07507c;
    --sky: #0aa6dd;
    --ink: #3b3f44;
    --soft-rule: rgba(255,255,255,0.45);
  }
  * { margin: 0; padding: 0; box-sizing: border-box; }
  html, body { width: 1200px; height: 900px; overflow: hidden; }
  body {
    background: var(--bg);
    font-family: "Roboto", sans-serif;
    display: flex;
    flex-direction: column;
    align-items: center;
    justify-content: center;
    gap: 36px;
  }
  .card {
    position: relative;
    width: 700px;
    height: 400px;
    border-radius: 22px;
    overflow: hidden;
  }
  /* Front */
  .card-front {
    background: linear-gradient(135deg, #ffffff 0%, var(--card-white) 60%, #e6e8ea 100%);
  }
  .brand {
    position: absolute;
    display: flex;
    align-items: center;
    gap: 16px;
  }
  .brand-dot {
    width: 70px; height: 70px;
    border-radius: 50%;
    border: 6px solid currentColor;
  }
  .brand-name {
    font-family: "Roboto", sans-serif;
    font-weight: 400;
    letter-spacing: 1px;
  }
  .card-front .brand { left: 60px; top: 48px; color: var(--navy); }
  .card-front .brand-name { font-size: 46px; }
  .front-rule {
    position: absolute;
    left: 50px; right: 50px; top: 160px;
    height: 2px;
    background: var(--navy);
  }
  .contact {
    position: absolute;
    left: 60px; top: 186px;
    list-style: none;
    font-size: 17px;
    color: var(--ink);
    line-height: 30px;
  }
  .contact li { display: flex; align-items: center; gap: 10px; }
  .contact svg { width: 14px; height: 14px; fill: var(--navy); }
  .contact strong { color: var(--navy); font-weight: 700; }
  .person {
    position: absolute;
    right: 56px; top: 188px;
    text-align: right;
  }
  .person-name {
    font-family: "Roboto Condensed", sans-serif;
    font-weight: 700;
    font-size: 30px;
    letter-spacing: 1px;
    color: var(--deep);
  }
  .person-name span { color: var(--sky); }
  .person-role { font-size: 17px; color: var(--ink); letter-spacing: 1px; }
  .address {
    position: absolute;
    right: 56px; top: 282px;
    text-align: right;
    font-size: 17px;
    line-height: 26px;
    color: var(--ink);
    letter-spacing: 1px;
  }
  .front-band { position: absolute; left: 0; bottom: 0; width: 700px; height: 70px; }

  /* Back */
  .card-back {
    background: linear-gradient(120deg, var(--sky) 0%, #0a7fb9 45%, var(--deep) 100%);
    color: #e9eef2;
    display: flex;
    flex-direction: column;
    align-items: center;
    padding-top: 40px;
  }
  .card-back .brand { position: static; color: #e9eef2; }
  .card-back .brand-name { font-size: 52px; font-weight: 300; }
  .services-title {
    margin-top: 26px;
    font-family: "Roboto Condensed", sans-serif;
    font-weight: 700;
    font-size: 28px;
    color: #dfe6ec;
  }
  .services-rule { width: 560px; height: 1px; background: var(--soft-rule); margin: 14px 0 12px; }
  .services-list {
    list-style: none;
    text-align: center;
    font-family: "Roboto Condensed", sans-serif;
    font-size: 17px;
    line-height: 26px;
    color: #f0f4f7;
  }
  .services-list li:first-child {
    border-bottom: 1px solid var(--soft-rule);
    padding-bottom: 8px;
    margin-bottom: 8px;
  }
</style>
</head>
<body>

<section class="card card-front">
  <div class="brand">
    <div class="brand-dot"></div>
    <div class="brand-name">TalkHarbor</div>
  </div>
  <div class="front-rule"></div>
  <ul class="contact">
    <li><svg viewBox="0 0 16 16"><path d="M3 1l3 3-2 2c1 2 3 4 5 5l2-2 3 3-2 3C6 14 2 10 1 3z"/></svg>(514) 555-0142</li>
    <li><svg viewBox="0 0 16 16"><path d="M1 3h14v10H1z M2 4l6 5 6-5v1L8 10 2 5z" fill-rule="evenodd"/></svg>DaniaKV@talkharbor.co.uk</li>
    <li><svg viewBox="0 0 16 16"><circle cx="8" cy="8" r="7"/></svg>www.<strong>talkharbor</strong>.co.uk</li>
  </ul>
  <div class="person">
    <div class="person-name">CORIN <span>VALE</span></div>
    <div class="person-role">Director</div>
  </div>
  <div class="address">42 Harbour Lane,<br>London, UK, E1 6AN</div>
  <svg class="front-band" viewBox="0 0 700 70" preserveAspectRatio="none" aria-hidden="true">
    <path d="M0 0 L300 38 Q320 40 335 30 L360 14 Q372 8 390 8 L700 8 L700 70 L0 70 Z" fill="var(--navy)"/>
    <path d="M0 -6 L300 34 L300 38 L0 4 Z" fill="var(--sky)"/>
  </svg>
</section>

<section class="card card-back">
  <div class="brand">
    <div class="brand-dot"></div>
    <div class="brand-name">TalkHarbor</div>
  </div>
  <h2 class="services-title">Our Services</h2>
  <div class="services-rule"></div>
  <ul class="services-list">
    <li>We offer highly customized coaching sessions and self-study content.</li>
    <li>Face to face language coaching sessions | On-line language coaching sessions</li>
    <li>Personalized Newsletters for self-learners | Language Learning Techniques Workshops</li>
    <li>Mindful Learning Workshops | Access to premium content, resources.</li>
  </ul>
</section>

</body>
</html>
```